Email Preference Page Design

We are looking for a 2 page design for our users to edit their email preferences and submit friend referrals. You can find the fuctionality, content and text here:

https://brightvanta.mailrelayhub.example/app/linkClick/7281/5fa9c1d3b07e442b/28374615/9bd4e01a7c3f2a65

* the shipping and billing address might be different so you need to show the billing if the "same as shipping" box is not checked. It can auto-hide like the page above shows if that fits your design.

* when the "unsubscribe from all email lists" box is selected, all the other checkbox options will hide as in the example page. We need you to show us what the site will look like with and without that checkbox selected.

We want to match these two pages to the general feel of these website pages:

www.brightvanta.com
and
free.brightvanta.com

The page should be very clean and tight. Project is for design only but must be able to be implemented in html showing button and checkbox states. Technically this must be two pages for our system - one for all the user info and one for individual email referrals (see example above).

Target Market(s)

video professionals

Industry/Entity Type

Shipping

Requirements
Must have
• our logo (see numerous versions attached)
well designed header
well designed sections
clean editable text
tight layout
html friendly
easy to understand
2 pages
Nice to have
• custom checkboxes and radio buttons

```html
<!DOCTYPE html>
<html lang="en">
<head>
<meta charset="utf-8">
<title>Subscriber Communication Preferences</title>
<link href="https://fonts.googleapis.com/css2?family=Lato:wght@400;700&display=swap" rel="stylesheet">
<style>
  :root {
    --page-bg: #ececeb;
    --card-bg: #ffffff;
    --card-border: #dcdcdc;
    --accent: #f07b1d;
    --text: #333333;
    --heading: #2f3a3f;
    --input-border: #c9c9c9;
    --rule: #d6d6d6;
    --cream-light: rgba(251, 241, 220, 0);
    --cream-mid: #fbf0d8;
    --cream-deep: #f7e4bd;
    --footer-band: #e7e5e1;
    --button-top: #fcd66a;
    --button-bottom: #f7bf3a;
    --button-border: #d99b22;
    --unsub-bg: #ebebea;
    --check-fill: #dfe6f3;
    --check-border: #6d7fa6;
    --check-mark: #2f3a6f;
  }
  * { box-sizing: border-box; margin: 0; padding: 0; }
  html, body { width: 695px; height: 1200px; overflow: hidden; }
  body {
    background: var(--page-bg);
    font-family: 'Lato', sans-serif;
    color: var(--text);
    position: relative;
  }
  .card {
    position: absolute;
    left: 56px;
    width: 582px;
    background: var(--card-bg);
    border: 1px solid var(--card-border);
    box-shadow: 0 1px 3px rgba(0,0,0,0.08);
    overflow: hidden;
  }
  .card--profile { top: 51px; height: 599px; }
  .card--lists { top: 659px; height: 482px; }

  .header-band {
    position: absolute; left: 0; top: 0; width: 100%; height: 82px;
    background: #f7f7f7;
  }
  .header-tab {
    position: absolute; left: 0; top: 0; width: 130px; height: 82px;
    background: var(--card-bg);
    border-top-right-radius: 14px;
  }
  .brand {
    position: absolute; left: 22px; top: 30px;
    display: flex; align-items: center; gap: 6px;
    font-size: 17px; font-weight: 700; color: var(--heading);
  }
  .brand-dot { width: 12px; height: 12px; border-radius: 50%; background: var(--accent); }
  .page-title {
    position: absolute; right: 20px; top: 9px;
    font-size: 17px; font-weight: 700; color: var(--accent);
    letter-spacing: 0.2px;
  }
  .header-rule {
    position: absolute; left: 0; top: 81px; width: 100%;
    border-top: 1px dotted var(--rule);
  }
  .section-title {
    position: absolute; display: flex; align-items: center; gap: 6px;
    font-size: 13px; font-weight: 400; color: var(--accent);
  }
  .field-label {
    position: absolute; font-size: 10px; text-align: right; width: 100px;
  }
  .field-input {
    position: absolute; width: 155px; height: 21px;
    border: 1px solid var(--input-border); border-radius: 2px; background: #fff;
  }
  .check-row {
    position: absolute; display: flex; align-items: center; gap: 7px;
    font-size: 10px; white-space: nowrap;
  }
  .box {
    width: 10px; height: 10px; border: 1px solid #9a9a9a; background: #f1f1f1;
    flex: none; position: relative;
  }
  .box--checked { background: var(--check-fill); border-color: var(--check-border); }
  .box--checked svg { position: absolute; left: 0; top: 0; }
  .note { color: var(--accent); }
  .cream-band {
    position: absolute; left: 0; bottom: 0; width: 100%; height: 88px;
    background: linear-gradient(to bottom, var(--cream-light) 0%, var(--cream-mid) 40%, var(--cream-deep) 100%);
  }
  .filter-heading {
    position: absolute; left: 72px; top: 62px;
    font-size: 14px; font-weight: 700; color: var(--heading);
  }
  .filter-sub {
    position: absolute; left: 72px; top: 89px;
    font-size: 13px; font-weight: 400; color: var(--accent);
  }
  .unsubscribe {
    position: absolute; left: 199px; top: 360px; width: 189px; height: 31px;
    background: var(--unsub-bg); border-radius: 2px;
    display: flex; align-items: center; justify-content: center; gap: 7px;
    font-size: 10px;
  }
  .footer-band {
    position: absolute; left: 0; bottom: 0; width: 100%; height: 67px;
    background: var(--footer-band);
  }
  .save-button {
    position: absolute; left: 218px; top: 17px; width: 156px; height: 35px;
    background: linear-gradient(var(--button-top), var(--button-bottom));
    border: 1px solid var(--button-border); border-radius: 3px;
    font-family: 'Lato', sans-serif; font-size: 12px; color: var(--heading);
  }
</style>
</head>
<body>

<section class="card card--profile">
  <div class="header-band"></div>
  <div class="header-tab"></div>
  <div class="brand"><span class="brand-dot"></span>brightvanta</div>
  <h1 class="page-title">SUBSCRIBER COMMUNICATION PREFERENCES</h1>
  <div class="header-rule"></div>

  <h2 class="section-title" style="left:72px;top:101px;">
    <svg width="9" height="12" viewBox="0 0 9 12"><path d="M4.5 0A4.5 4.5 0 0 0 0 4.5C0 8 4.5 12 4.5 12S9 8 9 4.5A4.5 4.5 0 0 0 4.5 0Zm0 6.3a1.8 1.8 0 1 1 0-3.6 1.8 1.8 0 0 1 0 3.6Z" fill="#f07b1d"/></svg>
    Contact information
  </h2>

  <label class="field-label" style="left:19px;top:150px;">First name</label><div class="field-input" style="left:128px;top:139px;"></div>
  <label class="field-label" style="left:19px;top:175px;">Email</label><div class="field-input" style="left:128px;top:164px;"></div>
  <label class="field-label" style="left:19px;top:199px;">Address line 1</label><div class="field-input" style="left:128px;top:188px;"></div>
  <label class="field-label" style="left:19px;top:226px;">Address line 3</label><div class="field-input" style="left:128px;top:215px;"></div>
  <label class="field-label" style="left:19px;top:258px;">Country</label><div class="field-input" style="left:128px;top:247px;"></div>
  <label class="field-label" style="left:19px;top:287px;">Postal code</label><div class="field-input" style="left:128px;top:276px;"></div>

  <label class="field-label" style="left:256px;top:152px;">Last name</label><div class="field-input" style="left:362px;top:139px;"></div>
  <label class="field-label" style="left:256px;top:178px;">Phone</label><div class="field-input" style="left:362px;top:166px;"></div>
  <label class="field-label" style="left:256px;top:206px;">Address line 2</label><div class="field-input" style="left:362px;top:194px;"></div>
  <label class="field-label" style="left:256px;top:234px;">City</label><div class="field-input" style="left:362px;top:222px;"></div>
  <label class="field-label" style="left:256px;top:263px;">State</label><div class="field-input" style="left:362px;top:251px;"></div>

  <h2 class="section-title" style="left:72px;top:329px;">
    <svg width="14" height="10" viewBox="0 0 14 10"><path d="M0 1h8v6H0Zm8 2h3l3 3v1H8Z" fill="#f07b1d"/><circle cx="3" cy="8.5" r="1.5" fill="#f07b1d"/><circle cx="11" cy="8.5" r="1.5" fill="#f07b1d"/></svg>
    Shipping Address
  </h2>
  <div class="check-row" style="left:72px;top:353px;"><span class="box"></span>My Billing address is same as shipping address.</div>

  <label class="field-label" style="left:19px;top:399px;">Address line 1</label><div class="field-input" style="left:128px;top:390px;"></div>
  <label class="field-label" style="left:19px;top:424px;">Address line 3</label><div class="field-input" style="left:128px;top:415px;"></div>
  <label class="field-label" style="left:19px;top:455px;">Country</label><div class="field-input" style="left:128px;top:446px;"></div>
  <label class="field-label" style="left:19px;top:486px;">Postal code</label><div class="field-input" style="left:128px;top:477px;"></div>

  <label class="field-label" style="left:256px;top:402px;">Address line 2</label><div class="field-input" style="left:362px;top:390px;"></div>
  <label class="field-label" style="left:256px;top:430px;">City</label><div class="field-input" style="left:362px;top:418px;"></div>
  <label class="field-label" style="left:256px;top:458px;">State</label><div class="field-input" style="left:362px;top:446px;"></div>

  <div class="cream-band" role="img" aria-label="Decorative soft cream wave background along the bottom of the contact panel"></div>
</section>

<section class="card card--lists">
  <div class="check-row" style="left:72px;top:34px;">
    <span class="box box--checked"><svg width="10" height="10" viewBox="0 0 10 10"><path d="M1.5 5 4 7.5 8.5 2" stroke="#2f3a6f" stroke-width="1.6" fill="none"/></svg></span>
    Subscribe me to your general email list&nbsp;&nbsp;<span class="note">This monthly email includes free video loops and VIP sale notices</span>
  </div>
  <h2 class="filter-heading">Help us filter our emails so we are only sending relevant informationto you</h2>
  <h3 class="filter-sub">Send me emails about these product types:</h3>

  <div class="check-row" style="left:72px;top:124px;"><span class="box"></span>Low energy motion loops</div>
  <div class="check-row" style="left:72px;top:145px;"><span class="box"></span>High energy motion loops</div>
  <div class="check-row" style="left:72px;top:167px;"><span class="box"></span>Timelapse footage</div>
  <div class="check-row" style="left:72px;top:188px;"><span class="box"></span>Worship or wedding motion loops</div>
  <div class="check-row" style="left:72px;top:209px;"><span class="box"></span>Pre-mixed DVDs and BluRay</div>
  <div class="check-row" style="left:72px;top:231px;"><span class="box"></span>Entertainment lasers for concerts and clubs</div>
  <div class="check-row" style="left:72px;top:252px;"><span class="box"></span>Entertainment lasers for text &amp; logo display</div>
  <div class="check-row" style="left:72px;top:273px;"><span class="box"></span>Custom logo animation services</div>
  <div class="check-row" style="left:72px;top:295px;"><span class="box"></span>Video software for creating video animations</div>
  <div class="check-row" style="left:72px;top:316px;"><span class="box"></span>Video software for live performance (Vjing)</div>

  <div class="check-row" style="left:319px;top:124px;"><span class="box"></span>VJing (live performance video)</div>
  <div class="check-row" style="left:319px;top:145px;"><span class="box"></span>DJing (live performance audio+video)</div>
  <div class="check-row" style="left:319px;top:167px;"><span class="box"></span>Performing in a band</div>
  <div class="check-row" style="left:319px;top:188px;"><span class="box"></span>Video editing</div>
  <div class="check-row" style="left:319px;top:209px;"><span class="box"></span>Corporate presentations</div>
  <div class="check-row" style="left:319px;top:231px;"><span class="box"></span>Worship video services</div>
  <div class="check-row" style="left:319px;top:252px;"><span class="box"></span>Lasers for entertainment &amp; branding</div>
  <div class="check-row" style="left:319px;top:273px;"><span class="box"></span>Special offers from BrightVanta partners</div>

  <div class="unsubscribe"><span class="box"></span>Unsubscribe me from all email lists</div>

  <div class="footer-band">
    <button class="save-button" type="button">Save My Preferences</button>
  </div>
</section>

</body>
</html>
```